Real estate broker business card

Want a modern celan but effective business card for my residential and commercial real estate business. I want the back of the card to advertise my services and to capture business. I have attached the back of my current business card fore ideas
Updates

Logos, photo and text updates added! Added Saturday, September 3, 2016

Project Deadline Extended Reason: LOGOS, PHOTOS AND TEST JUST UPLOADED! I'M READY TO PICK A DESIGN! THANK YOU! Added Saturday, September 3, 2016

Target Market(s)

home buyers and seller. commercial buyers and sellers

Industry/Entity Type

Real Estate

Contact Information for Business Card

must have my contact information and my photo

Requirements
Must have
• Carla Ventrino
• Owner & Qualifying Broker
• Ventrino Real Estate Services
• 505.718.2094
• carla@ventrinohomes.example
• www.ventrinohomes.example
Nice to have
• metallic
• Business capture text: " Don't buy or lease property without someone looking out for your best interests. I will represent you on your home or investment purchase for FREE!"
• "Home owners, call today to receive a FREE market analysis for your homes value!

```html
<!DOCTYPE html>
<html lang="en">
<head>
<meta charset="UTF-8">
<title>Carla Ventrino – Business Card</title>
<link rel="stylesheet" href="https://fonts.googleapis.com/css2?family=Cinzel:wght@500;600&family=Oswald:wght@500&family=Dosis:wght@500;600&display=swap">
<style>
  :root {
    --page-bg: #e9ebec;
    --silver-light: #f4f6f7;
    --silver-mid: #d9dfe2;
    --silver-dark: #c3ccd0;
    --teal-deep: #0d4a55;
    --teal-mid: #1d6b76;
    --teal-light: #3d8a93;
    --teal-text: #0f5360;
    --ink-dark: #283236;
    --band-text: #e8eff1;
    --band-soft: #e3cfd3;
    --photo-dark: #2d3b2f;
    --photo-light: #8d8478;
  }
  * { box-sizing: border-box; margin: 0; padding: 0; }
  html, body {
    width: 1200px; height: 969px; overflow: hidden;
    background: var(--page-bg);
  }
  .card {
    position: absolute; left: 100px; top: 199px;
    width: 1000px; height: 571px;
    border-radius: 6px; overflow: hidden;
    background: linear-gradient(160deg, var(--silver-light) 0%, var(--silver-mid) 45%, var(--silver-light) 70%, var(--silver-dark) 100%);
    box-shadow: 0 10px 30px rgba(0,0,0,.18);
  }
  .contact-band {
    position: absolute; left: 0; right: 0; top: 335px; bottom: 0;
    background: linear-gradient(180deg, var(--teal-mid) 0%, var(--teal-deep) 55%, var(--teal-light) 100%);
    border-top: 4px solid var(--teal-deep);
  }
  .portrait {
    position: absolute; left: 103px; top: 55px;
    width: 270px; height: 325px; border-radius: 16px;
    background: radial-gradient(ellipse at 50% 60%, var(--photo-light) 0%, var(--photo-dark) 75%);
  }
  .brand {
    position: absolute; left: 420px; top: 80px; width: 520px;
    display: flex; align-items: center; gap: 22px;
  }
  .brand-mark {
    width: 96px; height: 96px; flex: none;
    background: var(--teal-deep);
  }
  .brand-name {
    font-family: "Cinzel", serif; font-weight: 600;
    color: var(--teal-deep); line-height: 1;
  }
  .brand-name .primary { display: block; font-size: 62px; letter-spacing: 1px; }
  .brand-name .secondary { display: block; font-size: 21px; letter-spacing: 3px; margin-top: 8px; }
  .offer {
    position: absolute; left: 420px; top: 235px; width: 540px;
    font-family: "Oswald", sans-serif; font-weight: 500;
    font-size: 22px; line-height: 1.3; text-transform: uppercase;
    color: var(--teal-text); text-align: center; letter-spacing: .3px;
  }
  .identity {
    position: absolute; left: 30px; top: 395px; width: 420px; text-align: center;
  }
  .identity .person {
    font-family: "Cinzel", serif; font-weight: 500;
    font-size: 34px; color: var(--band-text); letter-spacing: 1px;
  }
  .identity .role {
    font-family: "Dosis", sans-serif; font-weight: 500;
    font-size: 25px; color: var(--band-soft); text-transform: uppercase;
    line-height: 1.35; letter-spacing: .5px;
  }
  .contacts {
    position: absolute; right: 50px; top: 405px;
    list-style: none; text-align: right;
    font-family: "Dosis", sans-serif; font-weight: 500;
    font-size: 25px; color: var(--band-text); letter-spacing: .5px;
  }
  .contacts li { display: flex; justify-content: flex-end; align-items: center; gap: 8px; height: 37px; }
  .contacts .lower { text-transform: uppercase; }
  .contacts svg { width: 22px; height: 22px; fill: var(--band-text); flex: none; }
</style>
</head>
<body>
  <article class="card">
    <div class="contact-band"></div>
    <div class="portrait" role="img" aria-label="Portrait photo of the broker"></div>

    <div class="brand">
      <div class="brand-mark"></div>
      <div class="brand-name">
        <span class="primary">VENTRINO</span>
        <span class="secondary">REAL ESTATE SERVICES</span>
      </div>
    </div>

    <p class="offer">Home owners, call today to receive<br>a free market analysis for your homes value!</p>

    <div class="identity">
      <p class="person">Carla Ventrino</p>
      <p class="role">Owner &amp; Qualifying Broker</p>
      <p class="role">Ventrino Real Estate Services</p>
    </div>

    <ul class="contacts">
      <li>505.718.2094
        <svg viewBox="0 0 24 24" aria-hidden="true"><path d="M6.6 10.8c1.4 2.8 3.8 5.1 6.6 6.6l2.2-2.2c.3-.3.7-.4 1-.2 1.1.4 2.3.6 3.6.6.6 0 1 .4 1 1V20c0 .6-.4 1-1 1C10.6 21 3 13.4 3 4c0-.6.4-1 1-1h3.5c.6 0 1 .4 1 1 0 1.3.2 2.5.6 3.6.1.3 0 .7-.2 1L6.6 10.8z"/></svg>
      </li>
      <li class="lower">carla@ventrinohomes.example
        <svg viewBox="0 0 24 24" aria-hidden="true"><path d="M2 5h20v14H2V5zm2 2v.4l8 5 8-5V7H4zm16 2.8-8 5-8-5V17h16V9.8z"/></svg>
      </li>
      <li class="lower">www.ventrinohomes.example
        <svg viewBox="0 0 24 24" aria-hidden="true"><path d="M12 2a10 10 0 1 0 0 20 10 10 0 0 0 0-20zm6.9 6h-3a15 15 0 0 0-1.3-3.9A8 8 0 0 1 18.9 8zM12 4c.8 1.2 1.5 2.5 1.9 4h-3.8c.4-1.5 1.1-2.8 1.9-4zM4.3 14a8 8 0 0 1 0-4h3.4a16 16 0 0 0 0 4H4.3zm.8 2h3a15 15 0 0 0 1.3 3.9A8 8 0 0 1 5.1 16zm3-8h-3a8 8 0 0 1 4.3-3.9A15 15 0 0 0 8.1 8zM12 20c-.8-1.2-1.5-2.5-1.9-4h3.8c-.4 1.5-1.1 2.8-1.9 4zm2.3-6H9.7a14 14 0 0 1 0-4h4.6a14 14 0 0 1 0 4zm.3 5.9a15 15 0 0 0 1.3-3.9h3a8 8 0 0 1-4.3 3.9zm1.7-5.9a16 16 0 0 0 0-4h3.4a8 8 0 0 1 0 4h-3.4z"/></svg>
      </li>
    </ul>
  </article>
</body>
</html>
```